Residential Mortgage Leader needs Wordpress Design

Looking for a home page website design for a client. We develop using the WordPress platform and would prefer the design be at least loosely based on an existing WordPress template. Attached files have many notes from our creative brief with client. The site must be responsive. Approved, basic wireframe attached. There is room for interpretation.

Existing web site: http://www.marisolkettering.example/

The Marisol Kettering Team relies on strong systems to deliver an on-time, done-right, friendly experience. Marisol offers mortgages and refinancing services throughout the United States. She is a successful Brookvale Funding agent who strives to be an active part of her community. She would like to focus the site on her team, rather than just her.

Difference makers...
When you work with the Marisol Kettering team you get a high level of expertise and a friendly experience.

She has amazing credentials. Marisol is widely recognized as a top producer for her company, and has earned a number of awards and honors for her customer service.

Marisol's team is very engaged and enjoys sharing social comments or photos from their community.

Imagery:
* Friendly, warm imagery, preferably of her team or an image to represent her team
* Clean and crisp
* Professional / Experts in mortgage and refinance
* Clean / Good use of white space
Updates

When possible, please use imagery from the DFW area. The client mentioned they would prefer not to see stock images. Thanks.

Amend that- creative use of stock images, however, is fine. A few designs have used stock imagery, but in a well-considered manner.

We added some photos and graphics that are local. We are Dallas / Ft. Worth, Plano, Frisco, Texas. We also added some examples of photos to use for the "In the Community" area. Stock photos of business folks just doesn't fit there. Thanks!

Target Market(s)

They service a lot of builders, but also work with homeowners. Their typical client is usually a woman searching for mortgage services online. She typically has a family and may refer her husband to Marisol's team. Keep in mind, however, they also see a number of other scenarios. Most of their clients are middle to high-end borrowers.

Industry/Entity Type

It Company

Requirements
Must have
• Design should be developed using program such as Photoshop or Fireworks or Illustrator as last preference. Ideally, the design would be based on an existing responsive WordPress theme, which we would customize. You must include the name of the target theme. The footer should include lots of space for disclaimers and legal language. Site navigation should include these choices: "Home, About, Builders, Mortgage Info, Approval, Blog, Contact"
Nice to have
• Blog, social media and photos area. Use of the already approved style prototype with colors and fonts (Lato- a Google font, Times New Roman and Cookie-a decorative Google font). However, we are open to interpretation.
Should not have
• Hard to read fonts or a lack of white space.

```html
<!DOCTYPE html>
<html lang="en">
<head>
<meta charset="utf-8">
<title>Brookvale Funding – Marisol Kettering Team</title>
<link rel="stylesheet" href="https://fonts.googleapis.com/css2?family=Roboto+Condensed:wght@300;400;700&family=Ubuntu:wght@500;700&family=Arimo:wght@400;700&family=Montserrat:wght@500&display=swap">
<style>
:root{
  --red:#c8191c;
  --red-dark:#9e1214;
  --blue:#1aa3e0;
  --blue-light:#2cc0f2;
  --blue-dark:#0a86c4;
  --ink:#1d1d1d;
  --text:#3a3a3a;
  --muted:#8a8a8a;
  --paper:#ffffff;
  --soft:#f6f6f6;
  --hero:#16181c;
  --footer:#1b1b1b;
  --footer-text:#c9c9c9;
  --hex:#3a3a3a;
}
*{box-sizing:border-box;margin:0;padding:0}
html,body{width:917px;height:1200px;overflow:hidden}
body{position:relative;background:var(--paper);font-family:"Arimo",Arial,sans-serif;color:var(--text)}
.abs{position:absolute}

/* header */
.site-header{left:0;top:0;width:917px;height:82px;background:linear-gradient(#fafafa,#ececec)}
.brand{left:107px;top:28px;display:flex;align-items:center;gap:8px}
.brand-name{font-family:"Ubuntu",sans-serif;font-weight:700;font-size:22px;color:var(--red);letter-spacing:-.3px}
.brand-dot{width:14px;height:14px;border-radius:50%;background:var(--red)}
.brand-sub{left:108px;top:55px;font-size:11px;color:#555}
.contact-top{right:107px;top:15px;text-align:right}
.contact-top .label{font-size:13px;color:var(--red);display:block}
.contact-top .phone{font-size:16px;color:var(--blue-dark);display:block;font-weight:700;letter-spacing:.2px}
.contact-top .mail{font-size:11px;color:var(--blue-dark);display:block;margin-top:9px}
.phone-icon{left:683px;top:17px}

/* nav */
.main-nav{left:0;top:82px;width:917px;height:38px;background:linear-gradient(#3fcdf7,#0fa6e2);border-bottom:1px solid #0a8dc8}
.main-nav ul{list-style:none;position:absolute;left:107px;top:0;display:flex;height:38px}
.main-nav li{font-family:"Montserrat",sans-serif;font-weight:500;font-size:12.5px;color:#fff;height:38px;line-height:38px;text-align:center;border-right:1px solid rgba(0,80,130,.35);box-shadow:1px 0 0 rgba(255,255,255,.25)}
.main-nav li:last-child{border-right:0;box-shadow:none}

/* hero */
.hero{left:0;top:120px;width:917px;height:307px;background:radial-gradient(ellipse at 40% 30%,#2c3036,var(--hero) 70%);overflow:hidden}
.hero-swoosh{left:0;top:0}
.hero-photo{left:108px;top:142px;width:327px;height:264px;background:#fff;padding:7px}
.hero-photo div{width:100%;height:100%;background:linear-gradient(#8b3a34 0%,#6f7b4a 35%,#4f7d3d 55%,#7b2e2c 80%,#3a2a28 100%)}
.hero-title{left:484px;top:178px;font-family:"Roboto Condensed",sans-serif;font-weight:700;font-size:29px;color:var(--blue);letter-spacing:-.2px}
.hero-copy{left:486px;top:228px;width:340px;font-family:"Roboto Condensed",sans-serif;font-weight:300;font-size:21px;line-height:25px;color:#fff}
.btn-start{left:485px;top:325px;width:126px;height:37px;border-radius:3px;background:linear-gradient(var(--blue-light),var(--blue-dark));font-family:"Montserrat",sans-serif;font-weight:500;font-size:19px;color:#10354a;text-align:center;line-height:37px}
.hero-alt{left:619px;top:336px;font-size:14px;color:#9a9a9a}

/* features */
.feature{top:463px;width:220px;text-align:center}
.feature-badge{width:64px;height:64px;border-radius:50%;background:var(--red);margin:0 auto;display:flex;align-items:center;justify-content:center}
.feature h2{font-family:"Ubuntu",sans-serif;font-weight:500;font-size:18px;color:var(--ink);margin-top:12px}
.feature p{font-size:10.5px;line-height:16px;color:#333;margin-top:7px}
.feature .more{display:inline-block;font-size:10px;color:var(--red);margin-top:8px;border-bottom:1px solid #e8a0a0}

/* community */
.community{left:0;top:662px;width:917px;height:273px;background:var(--soft)}
.community-title{left:0;top:674px;width:917px;text-align:center;font-family:"Roboto Condensed",sans-serif;font-size:27px;color:var(--red)}
.connect{left:107px;top:708px;width:703px;height:22px}
.connect .rule{position:absolute;top:11px;height:3px;border-top:1px solid #cfcfcf;border-bottom:1px solid #cfcfcf;width:265px}
.connect span{position:absolute;left:0;width:703px;text-align:center;font-family:"Roboto Condensed",sans-serif;font-size:17px;color:#333}
.col-title{font-family:"Ubuntu",sans-serif;font-weight:700;font-size:19px;color:var(--ink)}
.blog-list{list-style:none;margin-top:15px}
.blog-list li{font-size:10.5px;color:#333;height:23px;padding-left:11px;position:relative}
.blog-list li::before{content:"";position:absolute;left:1px;top:4px;border-left:4px solid #999;border-top:3px solid transparent;border-bottom:3px solid transparent}
.social-item{display:flex;gap:11px;margin-top:11px;height:40px}
.social-item:first-of-type{margin-top:16px}
.avatar{width:46px;height:40px;border:2px solid #fff;box-shadow:0 0 0 1px #ccc;background:linear-gradient(#b9a591,#4a3a33)}
.social-item p{font-size:10.5px;line-height:14.5px;color:#333;width:180px;margin-top:-3px}
.fan-box{left:584px;top:742px;width:226px;height:160px;background:#fff;border:1px solid #b9b9b9}
.fan-head{height:21px;background:#eef0f4;border-bottom:1px solid #c4c8d0;font-size:10px;font-weight:700;color:#222;padding:5px 4px}
.fan-page{display:flex;gap:5px;padding:8px 3px 0}
.fan-mark{width:40px;height:28px;display:flex;align-items:center;justify-content:center}
.fan-mark i{width:12px;height:12px;border-radius:50%;background:var(--red)}
.fan-name{font-size:10px;color:#3b5998}
.fan-like{margin-top:3px;width:33px;height:16px;border:1px solid #c4cde0;background:#eef0f6;font-size:8px;color:#3b5998;text-align:center;line-height:14px}
.fan-count{margin:10px 8px 0;padding-top:6px;border-top:1px solid #ddd;font-size:9px;color:#333}
.fan-faces{display:flex;gap:2px;padding:5px 8px 0}
.fan-faces div{width:36px;height:36px}
.fan-foot{margin:6px 8px 0;padding-top:4px;border-top:1px solid #ddd;font-size:7.5px;color:#555;display:flex;align-items:center;gap:4px}
.fan-foot i{width:8px;height:8px;background:#3b5998}

/* footer */
.site-footer{left:0;top:935px;width:917px;height:265px;background:var(--footer)}
.agent-photo{left:107px;top:956px;width:122px;height:145px;border:3px solid #2b2b2b;background:linear-gradient(#5a6b78 0%,#b98e74 45%,#c8302a 80%,#b22420 100%)}
.agent-name{left:251px;top:953px;font-family:"Roboto Condensed",sans-serif;font-weight:300;font-size:19px;color:#fff}
.agent-role{left:252px;top:977px;font-size:10.5px;font-weight:700;color:#e5e5e5}
.hex-icon{width:34px;height:38px}
.f-text{font-size:10px;line-height:16px;color:var(--footer-text)}
.f-text b{color:#fff}
.footer-title{font-family:"Roboto Condensed",sans-serif;font-weight:300;font-size:19px;color:#fff}
.quick-links{list-style:none;margin-top:9px}
.quick-links li{font-size:10px;color:var(--footer-text);height:18.7px}
.copyright{left:640px;top:1091px;width:190px;text-align:center;font-size:10px;line-height:19px;color:var(--footer-text)}
.footer-rule{left:107px;top:1138px;width:703px;border-top:1px solid #333}
.legal{left:107px;top:1150px;width:703px;text-align:center;font-size:10px;line-height:19px;color:var(--footer-text)}
</style>
</head>
<body>

<header class="site-header abs"></header>
<div class="brand abs"><span class="brand-name">Brookvale Funding</span><span class="brand-dot"></span></div>
<div class="brand-sub abs">A Harrowgate Company</div>
<svg class="phone-icon abs" width="14" height="30" viewBox="0 0 14 30" aria-hidden="true"><path d="M4 1h5v8H6c-1 4-1 8 0 12h3v8H4C0 21 0 9 4 1z" fill="var(--red)"/></svg>
<div class="contact-top abs">
  <span class="label">Work With Us</span>
  <span class="phone">(555) 014-7890</span>
  <span class="mail">mkettering@brookvalefunding.example</span>
</div>

<nav class="main-nav abs">
  <ul>
    <li style="width:65px">Home</li>
    <li style="width:67px">About</li>
    <li style="width:142px">Builder Information</li>
    <li style="width:160px">Mortgage Information</li>
    <li style="width:136px">Getting Approved</li>
    <li style="width:59px">Blog</li>
    <li style="width:74px">Contact</li>
  </ul>
</nav>

<section class="hero abs">
  <svg class="hero-swoosh abs" width="917" height="307" viewBox="0 0 917 307" aria-hidden="true">
    <path d="M917 0 C820 110 640 240 460 307 L530 307 C700 250 850 170 917 120 Z" fill="#8e1417"/>
    <path d="M917 120 C850 175 720 250 560 307 L917 307 Z" fill="#4a4d52"/>
    <path d="M917 170 C840 220 740 270 660 307 L917 307 Z" fill="#2a2c30"/>
  </svg>
</section>
<div class="hero-photo abs"><div role="img" aria-label="Marching band performing on a stadium field in front of a crowd"></div></div>
<h1 class="hero-title abs">Earning Your Business</h1>
<p class="hero-copy abs">The Marisol Kettering Team elies an Strong System to Deliver an&nbsp; on-time, done-right and Friendly experience.</p>
<div class="btn-start abs">Start Here</div>
<div class="hero-alt abs">- or - Get to Know Us</div>

<section class="feature abs" style="left:100px">
  <div class="feature-badge"><svg width="30" height="30" viewBox="0 0 30 30" aria-hidden="true"><path d="M6 15l6 6 12-12" fill="none" stroke="#fff" stroke-width="4" stroke-linecap="round" stroke-linejoin="round"/></svg></div>
  <h2>Our Credentials</h2>
  <p>Lorem Ipsum is simply dummy text of the printing and Lorem typesetting industry Lorem Ipsum.</p>
  <span class="more">Read More</span>
</section>
<section class="feature abs" style="left:348px">
  <div class="feature-badge"><svg width="32" height="32" viewBox="0 0 32 32" aria-hidden="true"><circle cx="16" cy="20" r="8" fill="#fff"/><path d="M10 3h5l2 9h-4zM22 3h-5l-2 9h4z" fill="#fff"/></svg></div>
  <h2>Awards</h2>
  <p>Lorem Ipsum is simply dummy text of the printing and Lorem typesetting industry Lorem Ipsum.</p>
  <span class="more">Read More</span>
</section>
<section class="feature abs" style="left:597px">
  <div class="feature-badge"><svg width="30" height="30" viewBox="0 0 30 30" aria-hidden="true"><rect x="4" y="6" width="19" height="19" rx="3" fill="none" stroke="#fff" stroke-width="2.5"/><path d="M12 18l2-5 10-10 3 3-10 10z" fill="#fff"/></svg></div>
  <h2>Recognion</h2>
  <p>Lorem Ipsum is simply dummy text of the printing and Lorem typesetting industry Lorem Ipsum.</p>
  <span class="more">Read More</span>
</section>

<section class="community abs"></section>
<h2 class="community-title abs">Engaged in Our Community</h2>
<div class="connect abs">
  <i class="rule" style="left:0"></i><i class="rule" style="right:0"></i>
  <span>Connect With us</span>
</div>

<div class="abs" style="left:106px;top:739px">
  <h3 class="col-title">Blog</h3>
  <ul class="blog-list">
    <li>Bomowing</li><li>Best Practices</li><li>Announcements</li><li>Resources</li><li>How to Guides</li><li>Builders Info</li>
  </ul>
</div>

<div class="abs" style="left:271px;top:739px">
  <h3 class="col-title">Social</h3>
  <div class="social-item"><div class="avatar" role="img" aria-label="Team member portrait"></div><p>Lorem Ipsum is simply dummy text of the printing and typesetting industry Lorem Ipsum.</p></div>
  <div class="social-item"><div class="avatar" role="img" aria-label="Team member portrait"></div><p>Lorem Ipsum is simply dummy text of the printing and typesetting industry Lorem Ipsum.</p></div>
  <div class="social-item"><div class="avatar" role="img" aria-label="Team member portrait"></div><p>Lorem Ipsum is simply dummy text of the printing and typesetting industry Lorem Ipsum.</p></div>
</div>

<aside class="fan-box abs">
  <div class="fan-head">Find us on Socialbook</div>
  <div class="fan-page">
    <div class="fan-mark"><i></i></div>
    <div><div class="fan-name">BROOKVALE FUNDING</div><div class="fan-like">Like</div></div>
  </div>
  <div class="fan-count">2,994 people like Brookvale Funding</div>
  <div class="fan-faces">
    <div role="img" aria-label="Follower photo" style="background:#c96a8a"></div>
    <div role="img" aria-label="Follower photo" style="background:#6b5a4a"></div>
    <div role="img" aria-label="Follower photo" style="background:#8a8a8a"></div>
    <div role="img" aria-label="Follower photo" style="background:#5a3a34"></div>
    <div role="img" aria-label="Follower photo" style="background:#a8323a"></div>
    <div role="img" aria-label="Follower photo" style="background:#7a3a3e"></div>
  </div>
  <div class="fan-foot"><i></i>Socialbook social plugin</div>
</aside>

<footer class="site-footer abs"></footer>
<div class="agent-photo abs" role="img" aria-label="Portrait of Marisol Kettering, branch manager"></div>
<div class="agent-name abs">Marisol Kettering,</div>
<div class="agent-role abs">Branch Manager</div>

<svg class="hex-icon abs" style="left:251px;top:1006px" viewBox="0 0 34 38" aria-hidden="true"><path d="M17 0l17 9.5v19L17 38 0 28.5v-19z" fill="var(--hex)"/><path d="M12 10h4l1 5-2 1c1 3 3 5 6 6l1-2 5 1v4c-9 1-16-6-15-15z" fill="#fff"/></svg>
<svg class="hex-icon abs" style="left:268px;top:1037px" viewBox="0 0 34 38" aria-hidden="true"><path d="M17 0l17 9.5v19L17 38 0 28.5v-19z" fill="var(--hex)"/><rect x="9" y="13" width="16" height="12" fill="#fff"/><path d="M9 13l8 7 8-7" fill="none" stroke="var(--hex)" stroke-width="1.5"/></svg>
<svg class="hex-icon abs" style="left:251px;top:1068px" viewBox="0 0 34 38" aria-hidden="true"><path d="M17 0l17 9.5v19L17 38 0 28.5v-19z" fill="var(--hex)"/><path d="M17 28c-5-6-7-9-7-12a7 7 0 0114 0c0 3-2 6-7 12z" fill="#fff"/><circle cx="17" cy="16" r="2.5" fill="var(--hex)"/></svg>
<div class="f-text abs" style="left:294px;top:1008px"><b>Office:</b> 555.010.5500<br><b>Cell:</b> 555.018.8830</div>
<div class="f-text abs" style="left:311px;top:1045px">mkettering@brookvalefunding.example</div>
<div class="f-text abs" style="left:294px;top:1078px">NMLS: 40219<br>4820 Cedar Row , Ste. 210<br>Frisco, TX 75099</div>

<div class="abs" style="left:507px;top:952px">
  <h3 class="footer-title">Quick Links</h3>
  <ul class="quick-links">
    <li>Home</li><li>About</li><li>Builder Information</li><li>Mortgage Information</li><li>Getting Approved</li><li>Blog</li><li>Contact</li>
  </ul>
</div>

<h3 class="footer-title abs" style="left:680px;top:952px">Follows Us:</h3>
<svg class="abs" style="left:680px;top:985px" width="112" height="38" viewBox="0 0 112 38" role="img" aria-label="Social network links">
  <path d="M18 0l17 9.5v19L18 38 1 28.5v-19z" fill="#4a4a4a"/>
  <path d="M56 0l17 9.5v19L56 38 39 28.5v-19z" fill="#4a4a4a"/>
  <path d="M94 0l17 9.5v19L94 38 77 28.5v-19z" fill="#4a4a4a"/>
</svg>
<svg class="abs" style="left:711px;top:1034px" width="46" height="44" viewBox="0 0 46 44" role="img" aria-label="Fair housing badge"><rect x="3" y="3" width="40" height="38" rx="2" fill="#555"/></svg>
<div class="copyright abs">© Copyright 2013 Brookvale Funding·<br>All Rights Reserved ·</div>

<div class="footer-rule abs"></div>
<p class="legal abs">In accordance with Section 326 of the USA PATRIOT Act of 2001, Brookvale Funding is required to obtain a copy of the documents used in identifying our new account customers. This notice is being provided to you for adequate notice given under this act.</p>

</body>
</html>
```